I need a website designed. I am a mortgage loan officer and would like to have a website for me and my team where i can post resources, videos and blog information for my clients. A website like themorvaskteam.com .

The theme is - The Pelkins Team - Home Loan Group powered by Brightwell Home Loans -

Target Market(s)

B2B (Real Estate Agents)and B2C (Home buyers and refinancing)

Industry/Entity Type

Mortgage Lender

Coding

Coded - Design and coding required

Number of Pages Required

5+ page

Font styles to use
Serif
Sans Serif

Colors

Designer to choose colors to be used in the design.

Requirements
Must have
• Disclaimers: Licensed by the Bureau of Lending Affairs under the Pacific Credit Providers Act. Loans made or arranged pursuant to a Pacific Credit Providers Act License. Equal Housing Lender Brightwell Cannot Accept mortgage applications for properties located in New York via this site
• Mobile Friendly
Nice to have
• Main Links: Home, About Us(see team flyer), Mortgage 101, Contact Us (formzig form)

```html
<!DOCTYPE html>
<html lang="en">
<head>
<meta charset="utf-8">
<title>The Pelkins Team – Home Loan Group</title>
<link href="https://fonts.googleapis.com/css2?family=Dosis:wght@500;600;700&family=Raleway:wght@400;500;600;700&display=swap" rel="stylesheet">
<style>
:root{
  --blue:#0f63b6;
  --navy:#232a72;
  --deep:#122c7a;
  --ink:#222;
  --text:#666;
  --band:#f3f4f6;
  --badge:#dfe2e7;
  --black:#050505;
  --white:#fff;
}
*{box-sizing:border-box;margin:0;padding:0}
html,body{width:1200px;height:3863px;overflow:hidden}
body{font-family:'Raleway',sans-serif;color:var(--text);background:var(--white);position:relative}
.abs{position:absolute}
.heading{font-family:'Dosis',sans-serif;font-weight:600;color:var(--ink);letter-spacing:1px;text-transform:uppercase}
.ph{position:absolute}

/* header */
.site-header{position:absolute;left:0;top:0;width:1200px;height:118px;background:var(--white);border-top:5px solid var(--blue);z-index:5}
.brand{position:absolute;left:100px;top:38px;display:flex;align-items:center;gap:12px}
.brand-square{display:block;width:26px;height:26px;background:var(--blue)}
.brand-name{font-family:'Raleway',sans-serif;font-weight:600;font-size:22px;color:var(--deep)}
.main-nav{position:absolute;right:105px;top:45px;display:flex;gap:62px;font-size:15px;font-weight:500;color:#333;text-transform:uppercase}
.main-nav .active{color:var(--blue)}

/* hero */
.hero{position:absolute;left:0;top:118px;width:1200px;height:690px;overflow:hidden}
.hero-photo{left:0;top:0;width:1200px;height:690px;background:linear-gradient(100deg,#9aa3ad 0%,#c9ced4 40%,#e7e9ec 70%,#d7d9dc 100%)}
.hero-title{left:0;top:180px;width:1200px;text-align:center;font-family:'Dosis',sans-serif;font-weight:600;font-size:60px;color:var(--white);letter-spacing:2px}
.hero-sub{left:0;top:262px;width:1200px;text-align:center;font-size:22px;color:var(--white)}
.hero-cta{left:505px;top:312px;width:190px;height:44px;border-radius:22px;background:var(--blue);color:var(--white);font-size:14px;font-weight:700;text-align:center;line-height:44px;text-transform:uppercase}
.slide-arrow{width:40px;height:40px;border-radius:50%;border:2px solid rgba(255,255,255,.8);color:var(--white);text-align:center;line-height:35px;font-size:20px}
.hero-wave{left:0;top:500px}

/* intro */
.intro{position:absolute;left:0;top:808px;width:1200px;height:455px}
.intro-photo{left:100px;top:15px;width:290px;height:290px;border-radius:12px;background:linear-gradient(160deg,#d5d9de,#8e8a86 55%,#2c3340)}
.intro-body{left:425px;top:18px;width:680px}
.intro-name{font-family:'Dosis',sans-serif;font-weight:600;font-size:28px;color:var(--ink);text-transform:uppercase}
.intro-role{font-size:16px;color:#444;margin:10px 0 14px}
.contact-list{list-style:none;font-size:13px;color:var(--blue)}
.contact-list li{display:flex;align-items:center;gap:12px;margin-bottom:10px}
.contact-list svg{width:13px;height:13px;fill:var(--blue)}
.intro-bio{font-size:12.5px;line-height:24px;color:#777;margin-top:14px}

/* team */
.team{position:absolute;left:0;top:1263px;width:1200px;height:797px;background:linear-gradient(180deg,#f2f6fb,#e8f0f9)}
.team .heading{position:absolute;left:0;top:100px;width:1200px;text-align:center;font-size:36px}
.member{position:absolute;top:256px;width:325px;height:460px;color:var(--white);text-align:center}
.member.blue{background:var(--blue)}
.member.navy{background:var(--navy)}
.avatar{position:absolute;left:82px;top:-80px;width:160px;height:160px;border-radius:50%;border:5px solid var(--white);background:linear-gradient(160deg,#e3e5e8,#8a8580 60%,#2e3440)}
.member-name{margin-top:112px;font-family:'Dosis',sans-serif;font-weight:600;font-size:21px;text-transform:uppercase}
.member-info{list-style:none;font-size:12px;margin-top:14px;line-height:28px}
.member-info svg{width:11px;height:11px;fill:var(--white);vertical-align:-1px;margin-right:8px}
.member-text{font-size:12px;line-height:22px;padding:0 30px;margin-top:20px;height:90px;overflow:hidden}
.member-btn{display:inline-block;margin-top:28px;width:132px;height:36px;line-height:36px;border-radius:18px;background:var(--navy);font-size:11px;font-weight:700;text-transform:uppercase}
.member.navy .member-btn{background:var(--blue)}

/* media */
.media{position:absolute;left:0;top:2060px;width:1200px;height:720px}
.media .heading{position:absolute;top:88px;font-size:32px}
.video-main{left:100px;top:145px;width:480px;height:305px;background:linear-gradient(135deg,#7a5a3e,#c49a6a 45%,#e6dccd)}
.video-small{top:460px;width:235px;height:200px;background:linear-gradient(135deg,#b9c7d6,#eef1f4)}
.play{position:absolute;left:50%;top:50%;transform:translate(-50%,-50%)}
.post{position:absolute;left:605px;width:500px;height:155px}
.post-thumb{left:0;top:0;width:205px;height:150px;background:linear-gradient(135deg,#8c99a6,#dfe3e7)}
.post-body{left:225px;top:8px;width:275px}
.post-title{font-family:'Dosis',sans-serif;font-weight:600;font-size:16px;color:var(--ink);text-transform:uppercase}
.post-text{font-size:12px;line-height:20px;color:#888;margin-top:10px}
.post-date{font-size:12px;color:var(--blue);margin-top:8px}
.post-date svg,.res-date svg{width:11px;height:11px;fill:var(--blue);vertical-align:-1px;margin-right:5px}

/* partners */
.partners{position:absolute;left:0;top:2780px;width:1200px;height:210px;background:var(--band)}
.badge{position:absolute;top:62px;width:155px;height:78px;background:var(--badge);border-radius:3px}
.chev{position:absolute;top:86px;font-size:26px;color:#333}

/* resources */
.resources{position:absolute;left:0;top:2990px;width:1200px;height:430px}
.resources .heading{position:absolute;left:0;top:78px;width:1200px;text-align:center;font-size:36px}
.res-thumb{top:160px;width:205px;height:180px;background:linear-gradient(135deg,#c98a66,#f0dccb)}
.res-body{top:160px;width:240px}
.res-title{font-size:18px;font-weight:500;color:var(--ink);line-height:24px}
.res-date{font-size:12px;color:var(--blue);margin:8px 0}
.res-text{font-size:12px;line-height:20px;color:#888}
.res-more{text-align:right;font-size:12px;color:var(--blue)}
.round-arrow{width:34px;height:34px;border-radius:50%;border:1px solid #ccc;color:#aaa;text-align:center;line-height:30px;font-size:18px}

/* footer */
.site-footer{position:absolute;left:0;top:3420px;width:1200px;height:443px;background:var(--black);color:#ddd}
.foot-brand{left:100px;top:108px;display:flex;align-items:center;gap:12px}
.foot-brand .brand-square{background:#3d7fd0}
.foot-brand .brand-name{color:#3d7fd0}
.eho{left:444px;top:92px;width:62px;height:62px;border:3px solid #ccc}
.foot-nav{left:535px;top:110px;width:565px;display:flex;justify-content:space-between;font-size:14px;font-weight:500;color:var(--white);text-transform:uppercase}
.foot-nav .sep{color:#888}
.foot-info{left:100px;top:282px;width:1000px;font-size:12px;line-height:26px;color:#ddd}
.foot-info svg{width:12px;height:12px;fill:#ddd;vertical-align:-1px;margin-right:8px}
</style>
</head>
<body>

<header class="site-header">
  <div class="brand">
    <span class="brand-square"></span>
    <span class="brand-name">The Pelkins Team</span>
  </div>
  <nav class="main-nav">
    <span class="active">Home</span><span>About Us</span><span>Mortgage 101</span><span>Contact Us</span>
    <svg width="16" height="16" viewBox="0 0 16 16" fill="none" stroke="#0f63b6" stroke-width="2.2"><circle cx="6.5" cy="6.5" r="4.8"/><path d="M10 10l4.5 4.5"/></svg>
  </nav>
</header>

<section class="hero">
  <div class="ph hero-photo" role="img" aria-label="Desk scene with hands reviewing papers beside a small model house with a red roof"></div>
  <h1 class="abs hero-title">PELKINS TEAM</h1>
  <p class="abs hero-sub">At vero eos et accusamus et iusto odio qui blanditiis</p>
  <div class="abs hero-cta">Call Us Today</div>
  <div class="abs slide-arrow" style="left:22px;top:248px">‹</div>
  <div class="abs slide-arrow" style="left:1138px;top:248px">›</div>
  <svg class="abs hero-wave" width="1200" height="190" viewBox="0 0 1200 190" preserveAspectRatio="none">
    <path d="M0 20 C250 150 520 150 760 90 C960 40 1100 40 1200 70 L1200 190 L0 190Z" fill="#122c7a"/>
    <path d="M0 70 C250 190 520 170 780 120 C980 80 1110 85 1200 110 L1200 190 L0 190Z" fill="#1c4fae"/>
    <path d="M0 100 C250 210 540 185 800 145 C1000 115 1120 125 1200 145 L1200 190 L0 190Z" fill="#ffffff"/>
  </svg>
</section>

<section class="intro">
  <div class="ph intro-photo" role="img" aria-label="Portrait of the producing branch manager"></div>
  <div class="abs intro-body">
    <h2 class="intro-name">Marco Pelkins</h2>
    <p class="intro-role">Producing Branch Manager</p>
    <ul class="contact-list">
      <li><svg viewBox="0 0 16 16"><path d="M8 1L0 8h2v7h4v-5h4v5h4V8h2z"/></svg>Brightwell Home Loans, Inc – NMLS 90210</li>
      <li><svg viewBox="0 0 16 16"><path d="M0 3h16v10H0z"/></svg>marco.pelkins@brightwellhomeloans.com</li>
      <li><svg viewBox="0 0 16 16"><path d="M3 1l3 3-2 2c1 2 3 4 5 5l2-2 3 3-2 3C6 15 1 10 0 4z"/></svg>Office: (555) 210-4418</li>
      <li><svg viewBox="0 0 16 16"><path d="M3 0h8v4H3z M0 5h16v7h-3v4H3v-4H0z"/></svg>Fax: (555) 210-4499</li>
    </ul>
    <p class="intro-bio">I have over 15 years of experience in Mortgage Planning. I rank in the top 1% of loan originators in the country. I pride myself on making the home buying process as smooth as possible. I will guide you through the mortgage process and look forward to helping you with your transaction. My team has been awarded with the Circle of Excellence award and CEO Club for being in the top 5 teams in the country having helped over 700+ families achieve the dream of home ownership between the years 2016 and 2017 and counting.</p>
  </div>
</section>

<section class="team">
  <h2 class="heading">Our Team</h2>

  <article class="member blue" style="left:100px">
    <div class="avatar" role="img" aria-label="Portrait of loan partner"></div>
    <h3 class="member-name">Tomas Reyna</h3>
    <ul class="member-info">
      <li><svg viewBox="0 0 16 16"><circle cx="8" cy="4.5" r="4"/><path d="M0 16c0-5 4-7 8-7s8 2 8 7z"/></svg>Loan Partner I - NMLS ID 7700418</li>
      <li><svg viewBox="0 0 16 16"><path d="M0 3h16v10H0z"/></svg>tomas.reyna@brightwellhomeloans.com</li>
      <li><svg viewBox="0 0 16 16"><path d="M3 1l3 3-2 2c1 2 3 4 5 5l2-2 3 3-2 3C6 15 1 10 0 4z"/></svg>(555) 210-4470</li>
    </ul>
    <p class="member-text">I am able to help customers with pre-qualifications and pre-approvals and keep the applicants and real estate agents informed during the application process.</p>
    <span class="member-btn">View Details</span>
  </article>

  <article class="member navy" style="left:440px">
    <div class="avatar" role="img" aria-label="Portrait of loan processor"></div>
    <h3 class="member-name">Luis Bernal</h3>
    <ul class="member-info">
      <li><svg viewBox="0 0 16 16"><circle cx="8" cy="4.5" r="4"/><path d="M0 16c0-5 4-7 8-7s8 2 8 7z"/></svg>Loan Processor – NMLS ID: 7700522</li>
      <li><svg viewBox="0 0 16 16"><path d="M0 3h16v10H0z"/></svg>luis.bernal@brightwellhomeloans.com</li>
      <li><svg viewBox="0 0 16 16"><path d="M3 1l3 3-2 2c1 2 3 4 5 5l2-2 3 3-2 3C6 15 1 10 0 4z"/></svg>(555) 210-4433</li>
    </ul>
    <p class="member-text">I verify loan documents including income, credit, appraisal and title insurance, preparing the loan application for submittal to underwriting. I review the loan file.</p>
    <span class="member-btn">View Details</span>
  </article>

  <article class="member blue" style="left:780px">
    <div class="avatar" role="img" aria-label="Portrait of closing coordinator"></div>
    <h3 class="member-name">Carla Menth</h3>
    <ul class="member-info">
      <li><svg viewBox="0 0 16 16"><circle cx="8" cy="4.5" r="4"/><path d="M0 16c0-5 4-7 8-7s8 2 8 7z"/></svg>Closing Coordinator- NMLS 7700634</li>
      <li><svg viewBox="0 0 16 16"><path d="M0 3h16v10H0z"/></svg>carla.menth@brightwellhomeloans.com</li>
      <li><svg viewBox="0 0 16 16"><path d="M3 1l3 3-2 2c1 2 3 4 5 5l2-2 3 3-2 3C6 15 1 10 0 4z"/></svg>(555) 210-4462</li>
    </ul>
    <p class="member-text">I guide our clients with any conditions or stipulations set by underwriting post loan conditional approval. I make sure all the transaction deadlines are met and help with preparing.</p>
    <span class="member-btn">View Details</span>
  </article>
</section>

<section class="media">
  <h2 class="heading" style="left:100px">Our Videos</h2>
  <div class="ph video-main" role="img" aria-label="Video still of a couple meeting a loan officer at a table">
    <svg class="play" width="56" height="56" viewBox="0 0 56 56"><circle cx="28" cy="28" r="28" fill="#e8202a"/><path d="M22 17l17 11-17 11z" fill="#fff"/></svg>
  </div>
  <div class="ph video-small" style="left:100px;top:460px" role="img" aria-label="Video still of a model house and keys">
    <svg class="play" width="44" height="44" viewBox="0 0 44 44"><circle cx="22" cy="22" r="20" fill="rgba(255,255,255,.35)" stroke="#fff" stroke-width="2"/><path d="M17 13l14 9-14 9z" fill="#fff"/></svg>
  </div>
  <div class="ph video-small" style="left:345px;top:460px" role="img" aria-label="Video still of coin stacks beside a model house">
    <svg class="play" width="44" height="44" viewBox="0 0 44 44"><circle cx="22" cy="22" r="20" fill="rgba(255,255,255,.35)" stroke="#fff" stroke-width="2"/><path d="M17 13l14 9-14 9z" fill="#fff"/></svg>
  </div>

  <h2 class="heading" style="left:605px">Blog Posts</h2>

  <article class="post" style="top:145px">
    <div class="ph post-thumb" role="img" aria-label="Two professionals shaking hands in an office"></div>
    <div class="abs post-body">
      <h3 class="post-title">Occaecati cupiditatevident</h3>
      <p class="post-text">Nor again is there anyone who loves or pursues or desires to obtain pain of itself, becau because occasionallanes.</p>
      <p class="post-date"><svg viewBox="0 0 16 16"><path d="M1 3h14v12H1z M4 0h2v4H4z M10 0h2v4h-2z"/></svg>November 10,2017</p>
    </div>
  </article>
  <article class="post" style="top:310px">
    <div class="ph post-thumb" role="img" aria-label="Model house on a desk with a calculator"></div>
    <div class="abs post-body">
      <h3 class="post-title">Debitis aut rerum necessit</h3>
      <p class="post-text">Nor again is there anyone who loves or pursues or desires to obtain pain of itself, becau because occasionallanes.</p>
      <p class="post-date"><svg viewBox="0 0 16 16"><path d="M1 3h14v12H1z M4 0h2v4H4z M10 0h2v4h-2z"/></svg>November 10,2017</p>
    </div>
  </article>
  <article class="post" style="top:475px">
    <div class="ph post-thumb" role="img" aria-label="Advisor meeting with clients at a desk"></div>
    <div class="abs post-body">
      <h3 class="post-title">Omnis voluptas assumenda</h3>
      <p class="post-text">Nor again is there anyone who loves or pursues or desires to obtain pain of itself, becau because occasionallanes.</p>
      <p class="post-date"><svg viewBox="0 0 16 16"><path d="M1 3h14v12H1z M4 0h2v4H4z M10 0h2v4h-2z"/></svg>November 10,2017</p>
    </div>
  </article>
</section>

<section class="partners" aria-label="Partners">
  <span class="chev" style="left:95px">‹</span>
  <div class="badge" style="left:135px" role="img" aria-label="Partner badge"></div>
  <div class="badge" style="left:300px" role="img" aria-label="Partner badge"></div>
  <div class="badge" style="left:465px" role="img" aria-label="Partner badge"></div>
  <div class="badge" style="left:630px" role="img" aria-label="Partner badge"></div>
  <div class="badge" style="left:795px" role="img" aria-label="Partner badge"></div>
  <div class="badge" style="left:960px;width:110px" role="img" aria-label="Partner badge"></div>
  <span class="chev" style="left:1090px">›</span>
</section>

<section class="resources">
  <h2 class="heading">Our Resources</h2>
  <div class="abs round-arrow" style="left:30px;top:236px">‹</div>
  <div class="abs round-arrow" style="left:1136px;top:236px">›</div>

  <div class="ph res-thumb" style="left:100px" role="img" aria-label="Smiling couple reviewing documents"></div>
  <div class="abs res-body" style="left:338px">
    <h3 class="res-title">Et harum quidem rerum facilis est</h3>
    <p class="res-date"><svg viewBox="0 0 16 16"><path d="M1 3h14v12H1z M4 0h2v4H4z M10 0h2v4h-2z"/></svg>April 19</p>
    <p class="res-text">At vero eos et accusamus et iusto odio dignissimos ducimus qui blanditiis praesentium voluptatum deleniti atque corrupti quos dolores et</p>
    <p class="res-more">[Read More]</p>
  </div>

  <div class="ph res-thumb" style="left:620px" role="img" aria-label="Couple smiling at a laptop"></div>
  <div class="abs res-body" style="left:860px">
    <h3 class="res-title">Nam libero tempore cum soluta nob</h3>
    <p class="res-date"><svg viewBox="0 0 16 16"><path d="M1 3h14v12H1z M4 0h2v4H4z M10 0h2v4h-2z"/></svg>April 18</p>
    <p class="res-text">At vero eos et accusamus et iusto odio dignissimos ducimus qui blanditiis praesentium voluptatum deleniti atque corrupti quos dolores et</p>
    <p class="res-more">[Read More]</p>
  </div>
</section>

<footer class="site-footer">
  <div class="abs foot-brand">
    <span class="brand-square"></span>
    <span class="brand-name">The Pelkins Team</span>
  </div>
  <div class="abs eho" role="img" aria-label="Equal housing lender badge"></div>
  <nav class="abs foot-nav">
    <span>Home</span><span class="sep">/</span><span>About Us</span><span class="sep">/</span><span>Mortgage 101</span><span class="sep">/</span><span>Contact Us</span>
  </nav>
  <div class="abs foot-info">
    <p><svg viewBox="0 0 16 16"><path d="M8 1L0 8h2v7h4v-5h4v5h4V8h2z"/></svg>2280 Alder Grove Rd, Suite 140, Lakeview FL 30415 &nbsp;&nbsp;&nbsp;&nbsp; <svg viewBox="0 0 16 16"><path d="M3 1l3 3-2 2c1 2 3 4 5 5l2-2 3 3-2 3C6 15 1 10 0 4z"/></svg>1-555-210-4470</p>
    <p style="margin-top:18px">Licensed by the Bureau of Lending Affairs under the Pacific Credit Providers Act. Loans made or arranged pursuant to a Pacific Credit Providers Act<br>License. Equal Housing Lender Brightwell Cannot Accept mortgage applications for properties located in New York via this site</p>
    <p style="margin-top:18px">© Copyright 2018. The Pelkins Team All Rights Reserved &nbsp;|&nbsp; Privacy policy &nbsp;|&nbsp; Terms and use</p>
  </div>
</footer>

</body>
</html>
```